Quill Harbor (IT/Network Services)

Quill Harbor, LLC provides technology services to small and medium businesses. Essentially, anytime you've every thought your business might need an "IT guy" to handle something you could instead call us to handle it. Basically, you can outsource your IT needs to us.

This is a brand new company and so we'll need a brand new website. I'd like to use WordPress to handle the site since that will make things easier for me to maintain in the long run.

The site should include a, more-or-less, static front page with the dynamic data occurring on pages linked from a navigational area.

I have a logo already designed that I would like to see used in the design. The one with "white" in the title is the official logo, just added some other versions for your perusal.

Color queues from the logo but feel free to add other colors where applicable.

The site should feel somewhat corporate but with a "younger" slant (something a 25-35 year old would enjoy).

Pages (either to be added initially or by me after design completion):
"About" section - includes company history, business philosophy, etc.
"Services" section - service options, service approach, service specifics
"Testimonials" section - (eventually)
"News" section - (eventually) industry news, company news, events, blog
Contact Links

Websites to view:
The two largest local competitors:
http://www.brightmarsh-tech.example/
http://www.kelvarworks.example/
Other local competitors:
http://www.tpbllc.example/
http://www.morrowfield.example/

Other info you might find useful:
Domain: qhllc.example
Address:
417 Elm Row S
Suite 512B
Nashville, TN 37288
Phone: 615-555-0187
Emails available for use/display:
info@qhllc.example
sales@qhllc.example

Target Market(s)

Our target clients are mainly small businesses (25 or less computer users) which means we're looking at a lot of start-ups or younger companies. We'll be interacting with many entrepreneurs and young business owners.

Requirements
Must have
• Need full WP theme (not a mockup)

```html
<!DOCTYPE html>
<html lang="en">
<head>
<meta charset="utf-8">
<title>Quill Harbor</title>
<link href="https://fonts.googleapis.com/css2?family=Yanone+Kaffeesatz:wght@400;500&family=Cardo&family=Arimo:ital,wght@0,400;1,700&display=swap" rel="stylesheet">
<style>
:root{
  --orange:#f0960a;
  --orange-dark:#d98300;
  --ink:#2b2b2b;
  --grey:#7a7a7a;
  --paper:#f4f3f1;
  --footer:#3c3c3c;
  --line:#c9c9c9;
}
*{margin:0;padding:0;box-sizing:border-box}
html,body{width:1200px;height:1092px;overflow:hidden;background:#fff}
body{position:relative;font-family:Arimo,Arial,sans-serif;color:var(--ink)}
.cond{font-family:"Yanone Kaffeesatz",sans-serif}
.header{position:absolute;top:0;left:0;width:1200px;height:104px}
.brand{position:absolute;left:88px;top:30px;display:flex;align-items:center;gap:12px;font-family:"Yanone Kaffeesatz",sans-serif;font-size:56px;font-weight:500;color:var(--grey);letter-spacing:1px}
.brand-dot{width:30px;height:30px;border-radius:50%;background:var(--orange)}
.search{position:absolute;left:861px;top:10px;width:220px;height:28px;background:#f1eeec;border:1px solid #e4e0dd}
.search svg{position:absolute;right:8px;top:6px}
.nav{position:absolute;top:42px;left:513px;display:flex;list-style:none}
.nav li{position:relative;height:50px}
.nav .tab{font-family:"Yanone Kaffeesatz",sans-serif;font-size:21px;color:#222;padding:2px 8px;border-radius:5px;display:inline-block}
.nav .tab small{font-size:14px;color:#555}
.nav .active .tab{background:var(--orange);color:#fff}
.nav .active .tab small{color:#fff}
.nav .sub{position:absolute;top:34px;left:4px;white-space:nowrap;font-family:"Yanone Kaffeesatz",sans-serif;font-size:16px;font-style:italic;letter-spacing:.3px;color:#222}
.hero{position:absolute;top:104px;left:0;width:1200px;height:397px;background:linear-gradient(var(--orange-dark),var(--orange))}
.hero-photo{position:absolute;left:88px;top:23px;width:538px;height:350px;background:#fff;box-shadow:0 1px 4px rgba(0,0,0,.35);padding:9px 9px 8px 10px}
.hero-photo div{width:100%;height:100%;background:linear-gradient(135deg,#e9eef3 0%,#9aa7b7 45%,#1c2a45 75%,#e7ecf1 100%)}
.hero h1{position:absolute;left:673px;top:50px;font-family:Cardo,serif;font-weight:400;color:#fff;font-size:32px;line-height:36px}
.hero h1 b{font-weight:400;font-size:40px}
.hero p{position:absolute;left:677px;top:138px;width:435px;color:#fff;font-size:13.5px;line-height:24px;text-align:justify}
.btn{position:absolute;display:flex;align-items:center;gap:8px;padding-left:13px;height:40px;width:99px;background:linear-gradient(#fff,#dcdcdc);border:1px solid #cfcfcf;font-style:italic;font-weight:700;font-size:19px;color:#8a8a8a}
.arrow{width:18px;height:18px;border-radius:50%;background:#e7e7e7;border:1px solid #cfcfcf;display:inline-flex;align-items:center;justify-content:center}
.dots{position:absolute;left:677px;top:318px;display:flex;gap:8px}
.dots i{width:16px;height:16px;border-radius:50%;background:#fff}
.dots i:first-child{background:radial-gradient(circle at 40% 35%,#555,#000)}
.features{position:absolute;top:501px;left:0;width:1200px;height:212px;background:var(--paper)}
.feature{position:absolute;top:22px;width:320px}
.feature .icon{width:61px;height:61px;border-radius:50%;border:5px solid #444;background:#fff;display:flex;align-items:center;justify-content:center}
.feature .icon span{width:35px;height:35px;border-radius:50%;background:#444}
.feature h2{position:absolute;left:72px;top:12px;font-family:"Yanone Kaffeesatz",sans-serif;font-weight:500;font-size:32px;white-space:nowrap}
.feature p{margin-top:8px;font-size:13.5px;line-height:24px;text-align:justify;color:#333}
.feature .arrow{vertical-align:middle;margin-left:10px}
.welcome-title{position:absolute;left:101px;top:713px;font-family:"Yanone Kaffeesatz",sans-serif;font-weight:500;font-size:32px}
.welcome{position:absolute;left:88px;top:745px;width:1020px;height:239px;border:1px solid var(--line);border-top:3px solid var(--orange)}
.welcome p{position:absolute;font-size:13.5px;line-height:24px;color:#222;text-align:justify}
.welcome-art{position:absolute;left:770px;top:22px;width:200px;height:212px;background:radial-gradient(circle at 35% 65%,#3a73d6 0,#1c46a8 35%,transparent 36%),linear-gradient(#fff,#fff)}
.footer{position:absolute;top:1000px;left:0;width:1200px;height:92px;background:var(--footer);color:#ddd}
.footer nav{position:absolute;left:88px;top:24px;font-family:"Yanone Kaffeesatz",sans-serif;font-size:15px;letter-spacing:.5px}
.footer small{position:absolute;left:88px;top:51px;font-family:"Yanone Kaffeesatz",sans-serif;font-size:15px;letter-spacing:.5px}
.social{position:absolute;top:23px;width:46px;height:46px;border-radius:4px}
</style>
</head>
<body>
<header class="header">
  <div class="brand"><span class="brand-dot"></span>QUILL HARBOR</div>
  <div class="search"><svg width="14" height="14" viewBox="0 0 14 14"><circle cx="8" cy="6" r="4.5" fill="none" stroke="#555" stroke-width="1.6"/><line x1="5" y1="9" x2="1.5" y2="12.5" stroke="#555" stroke-width="2"/></svg></div>
  <ul class="nav">
    <li class="active" style="width:120px"><span class="tab"><small>01</small> HOME</span><span class="sub">Welcome page</span></li>
    <li style="width:102px"><span class="tab"><small>02</small> ABOUT</span><span class="sub">Who We Are</span></li>
    <li style="width:130px"><span class="tab"><small>03</small> SOLUTIONS</span><span class="sub">What We Do</span></li>
    <li style="width:122px"><span class="tab"><small>04</small> SERVICES</span><span class="sub">What We Offer</span></li>
    <li><span class="tab"><small>05</small> CONTACT US</span><span class="sub">Stay in Touch</span></li>
  </ul>
</header>

<section class="hero">
  <div class="hero-photo"><div role="img" aria-label="Business people shaking hands in an office"></div></div>
  <h1><b style="font-size:32px">Build</b> <b>Your Business</b><br>With Us!</h1>
  <p>Lorem ipsum dolor sit amet, consectetur adipisicing elit, sed do eiusmod tempor incididunt ut labore et dolore magna aliqua. Ut enim ad minim veniam, quis nostrud exercitation ullamco laboris nisi ut aliquip ex ea commodo consequat.</p>
  <a class="btn" style="left:677px;top:252px">More <span class="arrow"><svg width="6" height="8"><path d="M1 1l3 3-3 3" stroke="#999" stroke-width="1.5" fill="none"/></svg></span></a>
  <div class="dots"><i></i><i></i><i></i><i></i><i></i></div>
</section>

<section class="features">
  <div class="feature" style="left:87px"><div class="icon"><span></span></div><h2>Effective Solutions</h2><p>Lorem ipsum dolor sit amet, consectetur adipisicing elit, sed do eiusmod tempor incididunt ut labore et dolore magna aliqua. Ut enim ad minim veniam, quis nostrud exercitation.<span class="arrow"><svg width="6" height="8"><path d="M1 1l3 3-3 3" stroke="#999" stroke-width="1.5" fill="none"/></svg></span></p></div>
  <div class="feature" style="left:433px;width:320px"><div class="icon"><span></span></div><h2 style="left:78px">Success Strategies</h2><p style="padding-left:5px">Lorem ipsum dolor sit amet, consectetur adipisicing elit, sed do eiusmod tempor incididunt ut labore et dolore magna aliqua. Ut enim ad minim veniam, quis nostrud exercitation.<span class="arrow"><svg width="6" height="8"><path d="M1 1l3 3-3 3" stroke="#999" stroke-width="1.5" fill="none"/></svg></span></p></div>
  <div class="feature" style="left:790px;width:318px"><div class="icon"><span></span></div><h2 style="left:79px">24/7 Support</h2><p style="padding-left:4px">Lorem ipsum dolor sit amet, consectetur adipisicing elit, sed do eiusmod tempor incididunt ut labore et dolore magna aliqua. Ut enim ad minim veniam, quis nostrud exercitation.<span class="arrow"><svg width="6" height="8"><path d="M1 1l3 3-3 3" stroke="#999" stroke-width="1.5" fill="none"/></svg></span></p></div>
</section>

<h2 class="welcome-title">Welcome to Our Website</h2>
<section class="welcome">
  <p style="left:11px;top:22px;width:738px">Lorem ipsum dolor sit amet, consectetur adipisicing elit, sed do eiusmod tempor incididunt ut labore et dolore magna aliqua. Ut enim ad minim veniam, quis nostrud exercitation.Lorem ipsum dolor sit amet, consectetur adipisicing elit, sed do eiusmod tempor incididunt ut labore et dolore magna aliqua. Ut enim ad minim veniam, quis nostrud exercitation.Lorem ipsum dolor sit amet, consectetur adipisicing elit, sed do eiusmod tempor incididunt ut labore et dolore magna aliqua. Ut enim ad minim veniam, quis nostrud exercitation.</p>
  <p style="left:7px;top:155px;width:460px;text-align:left">Lorem ipsum dolor sit amet, consectetur adipisicing elit, sed do eiusmod tempor incididunt ut labore et dolore magna aliqua.</p>
  <a class="btn" style="left:635px;top:170px;width:101px">More <span class="arrow"><svg width="6" height="8"><path d="M1 1l3 3-3 3" stroke="#999" stroke-width="1.5" fill="none"/></svg></span></a>
  <div class="welcome-art" role="img" aria-label="Businesswoman leaning on a blue globe"></div>
</section>

<footer class="footer">
  <nav>HOME | ABOUT &nbsp;| SOLUTIONS | SERVICES | CONTACT US</nav>
  <small>© 2012. ALL RIGHTS RESERVED.</small>
  <a class="social" style="left:1003px;background:#3b5a9a" aria-label="Social link"></a>
  <a class="social" style="left:1065px;background:#4fb8d8" aria-label="Social link"></a>
</footer>
</body>
</html>
```